Provide bookkeeping and accounting services to small and growing businesses

We need website and logo design using the name Dornaby as the logo.
The target audience are small companies and startups who need:
1) Simple bookkeeping services
2) Accounting advice that only someone with many years of senior financial experience as a CPA can provide.

The services are provided by two individuals. each of whom specialize in one of the areas.

We want the website to be clean without a lot of visual distraction but don't know how to make a boring subject interesting. We believe our potential clients, small business owners, need to find what they want quickly and easily without a lot of verbiage or distractions.

We've attached a draft of the homepage and have completed the text on most of the other pages.

Target Market(s)

small and early stage growth companies in San Diego North County

Industry/Entity Type

Accounting

Number of Pages Required

1 page

Font styles to use
Sans Serif

Colors
86cfc6
33b8a4
85cae6

Requirements
Must have
• We need a design for the website homepage that includes the name Dornaby as the logo. Must include a design for the name.
• Must have color in teal or greenish blue.
Nice to have
• White background, clean, clear, uncluttered.
• We would like to use the design in a Theme on a WordPress website. Themes Paper Lantern and Quiet Harbour are appealing to us.
Should not have
• Moving pictures

```html
<!DOCTYPE html>
<html lang="en">
<head>
<meta charset="utf-8">
<title>Dornaby Accounting &amp; Bookkeeping</title>
<link rel="stylesheet" href="https://fonts.googleapis.com/css2?family=Open+Sans:wght@300;400;600;700&display=swap">
<style>
:root{
  --teal:#33b8a4;
  --teal-soft:#86cfc6;
  --sky:#85cae6;
  --ink:#333a3f;
  --muted:#7b8287;
  --line:#e3e6e8;
  --dark:#1f2326;
  --darker:#15181a;
  --paper:#ffffff;
  --mist:#f4f6f7;
}
*{box-sizing:border-box;margin:0;padding:0}
html,body{width:1200px;height:2248px;overflow:hidden}
body{font-family:"Open Sans",Arial,sans-serif;color:var(--ink);background:var(--paper);font-size:13px;line-height:1.6}
.wrap{width:1000px;margin:0 auto;position:relative}
svg{display:block}

/* header */
.site-header{height:128px}
.site-header .wrap{display:flex;justify-content:space-between;align-items:center;height:128px}
.brand{display:flex;align-items:center;gap:14px}
.brand-mark{width:14px;height:14px;background:var(--teal)}
.brand-name{font-size:34px;font-weight:600;line-height:1.1;color:var(--ink)}
.header-contact{display:flex;gap:26px;font-size:12px;color:var(--muted);text-transform:uppercase}
.header-contact span{display:flex;align-items:center;gap:8px}
.header-contact .ico{width:26px;height:26px;border-radius:50%;background:var(--teal);display:flex;align-items:center;justify-content:center}

/* nav */
.main-nav{height:48px}
.main-nav ul{list-style:none;display:flex;background:var(--teal);height:48px}
.main-nav li{flex:1;text-align:center;line-height:48px;color:#fff;font-size:12px;font-weight:600;text-transform:uppercase;letter-spacing:.5px}
.main-nav li.active{background:var(--teal-soft)}

/* hero */
.hero{height:424px}
.hero-visual{height:424px;background:linear-gradient(120deg,#5c6468 0%,#9aa3a6 35%,#d7dcdc 60%,#8d979a 100%);position:relative}
.hero-caption{position:absolute;right:60px;top:200px;width:360px;background:rgba(51,184,164,.92);color:#fff;padding:16px 24px}
.hero-caption h2{font-size:30px;font-weight:400;line-height:1.2;margin-bottom:8px}
.hero-caption p{font-size:12px;line-height:1.5}
.hero-arrow{position:absolute;top:196px;width:30px;height:30px;border-radius:50%;background:rgba(255,255,255,.8);display:flex;align-items:center;justify-content:center}
.hero-arrow.prev{left:16px}.hero-arrow.next{right:16px}

/* welcome */
.welcome{padding:62px 0 0;height:220px;text-align:center}
.section-title{font-size:30px;font-weight:400;color:var(--ink)}
.rule{width:60px;height:2px;background:var(--teal);margin:10px auto 18px}
.welcome p{color:var(--muted);font-size:12.5px;max-width:880px;margin:0 auto}

/* cards */
.service-cards{height:228px}
.service-cards .wrap{display:flex;gap:20px}
.card{flex:1}
.card-visual{height:168px}
.card h3{text-align:center;font-size:14px;font-weight:600;color:var(--teal);padding-top:12px}

/* services */
.bookkeeping{height:402px;padding-top:36px}
.bookkeeping .wrap{display:flex;gap:44px}
.bk-main{flex:1}
.bk-main h2{font-size:28px;font-weight:400}
.bk-main .rule{margin:8px 0 14px}
.bk-main>p{color:var(--muted);font-size:12.5px;margin-bottom:24px}
.features{display:grid;grid-template-columns:1fr 1fr;gap:26px 34px}
.feature{display:flex;gap:14px}
.feature .ico{flex:none;width:44px;height:44px;border-radius:50%;border:2px solid var(--teal);display:flex;align-items:center;justify-content:center}
.feature h4{font-size:13.5px;font-weight:600;color:var(--teal)}
.feature p{font-size:11.5px;color:var(--muted);line-height:1.55}
.enquiry{width:280px;background:var(--mist);border:1px solid var(--line);padding-bottom:22px}
.enquiry h3{background:var(--teal);color:#fff;text-align:center;font-size:14px;font-weight:600;line-height:40px;letter-spacing:1px}
.enquiry form{padding:16px 22px 0;display:flex;flex-direction:column;gap:10px}
.field{height:30px;background:#fff;border:1px solid var(--line);font-size:11px;color:var(--muted);padding:0 10px;line-height:28px}
.field-row{display:flex;gap:8px}
.field-row .field{flex:1}
.field.area{height:58px}
.btn{display:inline-block;background:var(--teal);color:#fff;font-size:12px;font-weight:600;text-align:center;line-height:36px;text-transform:uppercase;letter-spacing:.5px}

/* about */
.about{height:280px;background:linear-gradient(180deg,#2b3033,#3e4548);text-align:center;color:#fff;padding-top:52px}
.about h2{font-size:30px;font-weight:400}
.about .rule{background:var(--teal-soft)}
.about p{font-size:12.5px;color:#d6dadc;max-width:840px;margin:0 auto 22px}
.about .btn{padding:0 28px}

/* partners */
.partners{height:170px;display:flex;align-items:center}
.partners .wrap{display:flex;justify-content:space-between;align-items:center;padding:0 40px}
.badge{width:96px;height:54px;border-radius:8px}

/* footer */
.site-footer{height:348px;background:var(--dark);color:#aeb4b7}
.footer-cols{display:flex;gap:40px;padding-top:40px;height:308px}
.footer-col{flex:1}
.footer-col h4{color:#fff;font-size:13px;font-weight:600;text-transform:uppercase;letter-spacing:.5px;margin-bottom:6px}
.footer-col .rule{margin:0 0 16px;width:40px}
.footer-col ul{list-style:none;font-size:11.5px;line-height:2}
.footer-col li{display:flex;align-items:center;gap:8px}
.dot{width:5px;height:5px;background:var(--teal);border-radius:50%;flex:none}
.social-dot{width:24px;height:24px;border-radius:50%;background:var(--teal);flex:none}
.copyright{height:40px;background:var(--darker);font-size:11px;color:#868c90;line-height:40px}
.copyright .wrap{display:flex;justify-content:space-between}
</style>
</head>
<body>

<header class="site-header">
  <div class="wrap">
    <div class="brand">
      <span class="brand-mark"></span>
      <div class="brand-name">Dornaby Accounting &amp;<br>Bookkeeping</div>
    </div>
    <div class="header-contact">
      <span><span class="ico"><svg width="12" height="12" viewBox="0 0 24 24"><path fill="#fff" d="M6.6 10.8a15 15 0 006.6 6.6l2.2-2.2c.3-.3.7-.4 1-.2 1.1.4 2.3.6 3.6.6.6 0 1 .4 1 1V20c0 .6-.4 1-1 1A17 17 0 013 4c0-.6.4-1 1-1h3.5c.6 0 1 .4 1 1 0 1.3.2 2.5.6 3.6.1.3 0 .7-.2 1z"/></svg></span>Call us: (555) 014-2290</span>
      <span><span class="ico"><svg width="12" height="12" viewBox="0 0 24 24"><circle cx="12" cy="8" r="4" fill="#fff"/><path fill="#fff" d="M4 21c0-4.4 3.6-7 8-7s8 2.6 8 7z"/></svg></span>Customer login / Register</span>
    </div>
  </div>
</header>

<nav class="main-nav">
  <ul class="wrap">
    <li class="active">Home</li><li>About us</li><li>Services</li><li>Resources</li><li>FAQ</li><li>Contact us</li>
  </ul>
</nav>

<section class="hero">
  <div class="wrap hero-visual" role="img" aria-label="Photo of a desk with a laptop, calculator, glasses and printed financial charts">
    <div class="hero-arrow prev"><svg width="10" height="12" viewBox="0 0 10 12"><path d="M8 1L2 6l6 5" stroke="#333" stroke-width="2" fill="none"/></svg></div>
    <div class="hero-arrow next"><svg width="10" height="12" viewBox="0 0 10 12"><path d="M2 1l6 5-6 5" stroke="#333" stroke-width="2" fill="none"/></svg></div>
    <div class="hero-caption">
      <h2>Bookkeeping Services</h2>
      <p>Clear and accurate books every month, so small business owners can focus on growth.</p>
    </div>
  </div>
</section>

<section class="welcome">
  <div class="wrap">
    <h2 class="section-title">Welcome</h2>
    <div class="rule"></div>
    <p>Dornaby offers a complete range of accounting and bookkeeping services to small and early stage companies in San Diego North County. We keep your records tidy, prepare reliable monthly reports and give practical advice drawn from many years of senior financial experience. Our two specialists each focus on one area, so you always speak with the right person. Whether you need simple bookkeeping or guidance from a seasoned CPA, we make it easy to find what you need quickly and get back to running your business with confidence.</p>
  </div>
</section>

<section class="service-cards">
  <div class="wrap">
    <div class="card"><div class="card-visual" role="img" aria-label="Photo of hands reviewing financial documents" style="background:linear-gradient(135deg,#cfe3ea,#7fa9bb)"></div><h3>Financials</h3></div>
    <div class="card"><div class="card-visual" role="img" aria-label="Photo of an advisor meeting with clients at a table" style="background:linear-gradient(135deg,#e6d9c8,#a8927a)"></div><h3>Accounting Advice</h3></div>
    <div class="card"><div class="card-visual" role="img" aria-label="Photo of a calculator and paperwork on a desk" style="background:linear-gradient(135deg,#eef0f0,#a9b2b5)"></div><h3>Accounting &amp; Bookkeeping</h3></div>
    <div class="card"><div class="card-visual" role="img" aria-label="Photo of a person writing figures in a ledger" style="background:linear-gradient(135deg,#e9e2d6,#b3a58f)"></div><h3>Payroll</h3></div>
  </div>
</section>

<section class="bookkeeping">
  <div class="wrap">
    <div class="bk-main">
      <h2>Bookkeeping Services</h2>
      <div class="rule"></div>
      <p>We handle the everyday numbers so you do not have to. From recording transactions to reconciling accounts, our bookkeeping keeps your business ready for tax time and for every decision in between.</p>
      <div class="features">
        <div class="feature"><span class="ico"><svg width="20" height="20" viewBox="0 0 24 24"><path d="M4 12l5 5L20 6" stroke="#33b8a4" stroke-width="2.5" fill="none"/></svg></span><div><h4>Monthly reconciliations</h4><p>Bank and card accounts matched each month so your balances are always correct and current.</p></div></div>
        <div class="feature"><span class="ico"><svg width="20" height="20" viewBox="0 0 24 24"><circle cx="12" cy="12" r="8" stroke="#33b8a4" stroke-width="2" fill="none"/><path d="M12 7v5l3 3" stroke="#33b8a4" stroke-width="2" fill="none"/></svg></span><div><h4>Timely reporting</h4><p>Clear profit and loss statements and balance sheets delivered on schedule every single month.</p></div></div>
        <div class="feature"><span class="ico"><svg width="20" height="20" viewBox="0 0 24 24"><path d="M5 19V11M12 19V6M19 19v-9" stroke="#33b8a4" stroke-width="2.5" fill="none"/></svg></span><div><h4>Cash flow insight</h4><p>Simple summaries that show where money comes from, where it goes and what lies ahead.</p></div></div>
        <div class="feature"><span class="ico"><svg width="20" height="20" viewBox="0 0 24 24"><rect x="5" y="4" width="14" height="16" rx="1" stroke="#33b8a4" stroke-width="2" fill="none"/><path d="M8 9h8M8 13h8M8 17h5" stroke="#33b8a4" stroke-width="2"/></svg></span><div><h4>Tax ready records</h4><p>Organized files and receipts so year end filing is fast, accurate and free of surprises.</p></div></div>
      </div>
    </div>
    <aside class="enquiry">
      <h3>ENQUIRY FORM</h3>
      <form>
        <div class="field">Name*</div>
        <div class="field">E-mail*</div>
        <div class="field">Phone*</div>
        <div class="field-row"><div class="field">Service</div><div class="field">Business</div></div>
        <div class="field-row"><div class="field">Date</div><div class="field">Time</div></div>
        <div class="field area">Message</div>
        <div class="btn">Get a free quote</div>
      </form>
    </aside>
  </div>
</section>

<section class="about" role="img" aria-label="Dark photo of financial paperwork behind the about text">
  <div class="wrap">
    <h2>About to Dornaby Accounting &amp; Bookkeeping</h2>
    <div class="rule"></div>
    <p>Dornaby was founded by two finance professionals who believe small businesses deserve the same quality of advice as large firms. One partner leads our bookkeeping work, the other brings decades of senior CPA experience to planning and strategy.</p>
    <span class="btn">Read more</span>
  </div>
</section>

<section class="partners">
  <div class="wrap">
    <span class="badge" style="background:#d9534f"></span>
    <span class="badge" style="background:#8bc34a"></span>
    <span class="badge" style="background:#f0a030"></span>
    <span class="badge" style="background:#9aa3a6"></span>
    <span class="badge" style="background:#3d6fb6"></span>
    <span class="badge" style="background:#e0b020"></span>
    <span class="badge" style="background:#4a90c8"></span>
  </div>
</section>

<footer class="site-footer">
  <div class="wrap footer-cols">
    <div class="footer-col"><h4>Navigation</h4><div class="rule"></div>
      <ul><li><span class="dot"></span>Home</li><li><span class="dot"></span>Services</li><li><span class="dot"></span>About us</li><li><span class="dot"></span>Resources</li><li><span class="dot"></span>FAQ</li><li><span class="dot"></span>Contact us</li></ul></div>
    <div class="footer-col"><h4>Accounting Office</h4><div class="rule"></div>
      <ul><li><span class="dot"></span>Dornaby Accounting &amp; Bookkeeping</li><li><span class="dot"></span>240 Harbor Lane, Suite 5</li><li><span class="dot"></span>Phone: (555) 014-2290</li><li><span class="dot"></span>hello@dornaby-books.com</li></ul></div>
    <div class="footer-col"><h4>Working Hours</h4><div class="rule"></div>
      <ul><li>We are open during the week to help with your books.</li><li><span class="dot"></span>Monday - Friday: 9am - 5pm</li><li><span class="dot"></span>Saturday: 10am - 2pm</li><li><span class="dot"></span>Sunday: Closed</li></ul></div>
    <div class="footer-col"><h4>Follow Us</h4><div class="rule"></div>
      <ul><li><span class="social-dot"></span>Social</li><li><span class="social-dot"></span>Updates</li><li><span class="social-dot"></span>Network</li></ul></div>
  </div>
  <div class="copyright"><div class="wrap"><span>Copyright &copy; Dornaby Accounting &amp; Bookkeeping. All rights reserved.</span><span>Top</span></div></div>
</footer>

</body>
</html>
```